Marlowby Services Website Design

We have most content but require a professional design. We have a logo already and will need it utilized along with several of the photos from the attached documentation.
First page should have our mission and Vision and the synapsis provided in the word document. Visitors will be prompted to select from one of our 3 divisions from this page.
Each division will have the same list of tabs : About, Services, Safety, Careers and Contact.
Photos on each divisions page should be representative of the divisions offerings. The word doc attached contains the requested content and we are open to edits that would complement and fill the website.
I like the Quorvane site www.quorvane.example - they are our competition so cant be modeled directly after this.
Please include prompts to request quote at each service page. align the format of the geotechnical page to the other 2 divisions.
I used chat gpt for some of the content so will need it optimized for SCO.

```html
<!DOCTYPE html>
<html lang="en">
<head>
<meta charset="utf-8">
<title>Marlowby Services</title>
<link href="https://fonts.googleapis.com/css2?family=Montserrat:wght@400;500;600;700;800&display=swap" rel="stylesheet">
<style>
:root{
  --red:#e31e24;
  --black:#0b0b0b;
  --ink:#1c1c1c;
  --grey:#e6e6e6;
  --white:#ffffff;
  --soil:#6b5235;
}
*{margin:0;padding:0;box-sizing:border-box}
html,body{width:1200px;height:3651px;overflow:hidden}
body{position:relative;font-family:"Montserrat",sans-serif;color:var(--ink);background:var(--white)}
.abs{position:absolute}
.topbar{left:0;top:0;width:1200px;height:51px;background:var(--black);color:var(--white);font-size:14px}
.topbar .item{position:absolute;top:17px;display:flex;align-items:center;gap:10px}
.nav{left:0;top:51px;width:1200px;height:129px;background:var(--white)}
.nav a{position:absolute;top:54px;font-size:16px;color:var(--ink);text-decoration:none;letter-spacing:.5px}
.nav a.active{color:var(--red)}
.brand{position:absolute;font-weight:800;color:var(--red);letter-spacing:4px;white-space:nowrap}
.nav .brand{left:390px;top:34px;width:414px;text-align:center;font-size:54px}
.hero{left:0;top:180px;width:1200px;height:630px;background:linear-gradient(180deg,#4f6a8a 0%,#6c6a58 22%,#7a5e3f 45%,var(--soil) 100%)}
.hero-title{right:111px;top:138px;text-align:right;color:var(--white);font-weight:800;font-size:41px;line-height:42px;letter-spacing:1px}
.hero-copy{right:111px;top:250px;width:330px;text-align:right;color:var(--white);font-size:16px;line-height:26px}
.btn{position:absolute;background:var(--red);color:var(--white);font-size:16px;text-align:center;letter-spacing:.5px;text-decoration:none}
.hero .btn{right:111px;top:406px;width:154px;height:38px;line-height:38px}
.h2{position:absolute;font-weight:800;color:var(--red);font-size:42px;letter-spacing:1.5px;line-height:1}
.lead{position:absolute;font-size:16px;line-height:26px}
.division{position:absolute;top:960px;width:300px;text-align:center}
.division .photo{position:absolute;left:47px;top:0;width:206px;height:206px;border-radius:50%;border:5px solid var(--red)}
.division .num{position:absolute;left:116px;top:164px;width:68px;height:68px;border-radius:50%;background:var(--red);border:4px solid var(--white);color:var(--white);font-weight:800;font-size:34px;line-height:60px}
.division h3{position:absolute;left:0;top:272px;width:300px;font-weight:500;font-size:21px;color:var(--red)}
.division p{position:absolute;left:0;top:320px;width:300px;font-size:16px;line-height:26px}
.band{left:0;width:1200px;background:var(--grey)}
.framed{position:absolute;border:5px solid var(--red)}
.mission-copy{left:601px;top:1590px;width:490px;font-size:16px;line-height:31px}
.services-intro{left:120px;top:2188px;width:960px;text-align:center;font-size:16px;line-height:31px}
.card{position:absolute;top:2324px;width:310px}
.card .photo{width:303px;height:262px}
.card h4{margin-top:30px;font-weight:600;font-size:17px;color:var(--red);letter-spacing:.5px}
.card p{margin-top:6px;font-size:12px;line-height:24px;color:#555}
.card a{display:inline-block;margin-top:6px;font-size:13px;font-weight:700;color:var(--red);text-decoration:underline}
.arrow{position:absolute;top:2437px;width:35px;height:35px}
.vision-copy{left:112px;top:2972px;width:500px;font-size:18px;line-height:31px}
.footer-nav{left:0;top:3545px;width:1200px;display:flex;justify-content:center;align-items:center;color:var(--white);font-size:16px}
.footer-nav span.sep{width:1px;height:18px;background:var(--white);margin:0 42px}
.copyright{left:0;top:3616px;width:1200px;text-align:center;color:var(--white);font-size:16px;letter-spacing:.5px}
</style>
</head>
<body>

<div class="abs topbar">
  <div class="item" style="left:112px">
    <svg width="18" height="18" viewBox="0 0 18 18" fill="none" stroke="#fff" stroke-width="1.5"><circle cx="9" cy="9" r="7.5"/><path d="M9 4.5V9l3 2"/></svg>
    <span>Mon - Sat : 08.00-21.00</span>
  </div>
  <div class="item" style="left:492px">
    <svg width="24" height="16" viewBox="0 0 24 16" fill="none" stroke="#fff" stroke-width="1.5"><rect x="1" y="1" width="22" height="14"/><path d="M1 1l11 8 11-8"/></svg>
    <span>hello@marlowby.example</span>
  </div>
  <div class="item" style="left:932px">
    <svg width="24" height="22" viewBox="0 0 24 24" fill="none" stroke="#fff" stroke-width="1.5"><path d="M5 3h4l2 5-3 2a12 12 0 0 0 6 6l2-3 5 2v4a2 2 0 0 1-2 2A18 18 0 0 1 3 5a2 2 0 0 1 2-2z"/><path d="M15 3a6 6 0 0 1 6 6M15 7a2 2 0 0 1 2 2"/></svg>
    <span>(800) 555-0142</span>
  </div>
</div>

<nav class="abs nav">
  <a class="active" href="#" style="left:111px">Home</a>
  <a href="#" style="left:187px">About</a>
  <a href="#" style="left:266px">Services</a>
  <div class="brand">MARLOWBY</div>
  <a href="#" style="left:845px">Safety</a>
  <a href="#" style="left:927px">Careers</a>
  <a href="#" style="left:1021px">Contact</a>
</nav>

<section class="abs hero" role="img" aria-label="White aerial lift truck parked on a gravel yard under a blue sky">
  <h1 class="abs hero-title">WELCOME TO<br>MARLOWBY</h1>
  <p class="abs hero-copy">Marlowby Lorem Ipsum is simply dummy text of the printing and typesetting industry. Lorem Ipsum has been the industry's standard dummy text ever since the 1500s</p>
  <a class="btn" href="#">GET STARTED</a>
</section>
<svg class="abs" style="left:0;top:670px" width="1200" height="150" viewBox="0 0 1200 150">
  <polygon points="0,7 750,77 1098,107 1200,7 1200,150 0,150" fill="#fff"/>
  <polygon points="1098,107 1200,7 1200,60 1145,140 750,77" fill="#e31e24"/>
</svg>

<h2 class="h2" style="left:110px;top:802px">SELECT DIVISION</h2>
<p class="lead" style="left:110px;top:872px;width:700px">Lorem Ipsum is simply dummy text of the printing and typesetting industry. Lorem Ipsum has been the industry's standard dummy text since the 1500s</p>

<div class="division" style="left:99px">
  <div class="photo" role="img" aria-label="Aerial lift truck in a yard" style="background:linear-gradient(180deg,#6f8aa8,#8a8a7a 40%,#6b5a45)"></div>
  <div class="num">1</div>
  <h3>Aerial Access</h3>
  <p>Lorem Ipsum is simply dummy text of the printing and typesetting industry. Lorem Ipsum</p>
</div>
<div class="division" style="left:450px">
  <div class="photo" role="img" aria-label="Overhead view of a drilling rig on a roadside" style="background:linear-gradient(180deg,#5e6a52,#8c8c84 50%,#6c6659)"></div>
  <div class="num">2</div>
  <h3>Geotechnical Drilling</h3>
  <p>Lorem Ipsum is simply dummy text of the printing and typesetting industry. Lorem Ipsum</p>
</div>
<div class="division" style="left:794px">
  <div class="photo" role="img" aria-label="Aerial view of equipment yard and roadway" style="background:linear-gradient(180deg,#5d6456,#7a7b72 50%,#555a4e)"></div>
  <div class="num">3</div>
  <h3>Renewable Energy Services</h3>
  <p>Lorem Ipsum is simply dummy text of the printing and typesetting industry. Lorem Ipsum</p>
</div>

<section class="abs band" style="top:1437px;height:599px"></section>
<div class="framed" role="img" aria-label="Lift truck with boom stowed, seen from above" style="left:112px;top:1494px;width:303px;height:238px;background:linear-gradient(160deg,#d9dde0,#a9a49a 50%,#7c6a52)"></div>
<div class="framed" role="img" aria-label="White truck with aerial lift on dirt ground" style="left:167px;top:1695px;width:303px;height:238px;background:linear-gradient(160deg,#8f7c62,#b7b2aa 50%,#7a6650)"></div>
<h2 class="h2" style="left:601px;top:1520px">MISSION STATEMENT</h2>
<p class="abs mission-copy">At Marlowby, our mission is to deliver unparalleled aerial access, geotechnical drilling, and service and maintenance solutions, consistently exceeding our clients' expectations. We strive to achieve this by investing in cutting-edge technology, fostering a culture of safety and continuous improvement, and prioritizing environmental sustainability. Through collaboration, integrity, and dedication, we aim to contribute to the success of our clients while maintaining the highest standards of quality and professionalism.</p>
<a class="btn" href="#" style="left:601px;top:1927px;width:153px;height:38px;line-height:38px">READ MORE</a>

<h2 class="h2" style="left:0;top:2117px;width:1200px;text-align:center">MARLOWBY SERVICES</h2>
<p class="abs services-intro">At Marlowby, our mission is to deliver unparalleled aerial access, geotechnical drilling, and service and maintenance solutions, consistently exceeding our clients' expectations. We strive to achieve this by investing in cutting-edge technology, fostering a culture of safety and continuous improvement, and prioritizing</p>

<svg class="arrow" style="left:39px" viewBox="0 0 35 35" fill="none" stroke="#e31e24" stroke-width="1.5"><circle cx="17.5" cy="17.5" r="16.5"/><path d="M20 11l-6 6.5 6 6.5"/></svg>
<svg class="arrow" style="left:1125px" viewBox="0 0 35 35" fill="none" stroke="#e31e24" stroke-width="1.5"><circle cx="17.5" cy="17.5" r="16.5"/><path d="M15 11l6 6.5-6 6.5"/></svg>

<div class="card" style="left:112px">
  <div class="photo" role="img" aria-label="Lift truck on a dirt lot from above" style="background:linear-gradient(160deg,#a08866,#8a7458 60%,#6f5c45)"></div>
  <h4>DELIVERING SAFE</h4>
  <p>Lorem ipsum dolor sit amet, consectetur adiasru dolor dolor, efficitur nec rhoncus non, pretiu ithsi tesque habitant morbi tristique</p>
  <a href="#">READ MORE</a>
</div>
<div class="card" style="left:447px">
  <div class="photo" role="img" aria-label="Extended boom beside a water tower against blue sky" style="background:linear-gradient(180deg,#3f7fc4,#79a9dc 70%,#6b7a5a)"></div>
  <h4>CONSTRUCTION</h4>
  <p>Lorem ipsum dolor sit amet, consectetur adiasru dolor dolor, efficitur nec rhoncus non, pretiu ithsi tesque habitant morbi tristique</p>
  <a href="#">READ MORE</a>
</div>
<div class="card" style="left:781px">
  <div class="photo" role="img" aria-label="Lift truck casting a long shadow on gravel" style="background:linear-gradient(160deg,#9a8468,#7a6650 60%,#5e4e3c)"></div>
  <h4>RENEWABLE ENERGY INDUSTRIES.</h4>
  <p>Lorem ipsum dolor sit amet, consectetur adiasru dolor dolor, efficitur nec rhoncus non, pretiu ithsi tesque habitant morbi tristique</p>
  <a href="#">READ MORE</a>
</div>

<section class="abs band" style="top:2815px;height:500px"></section>
<h2 class="h2" style="left:110px;top:2900px">OUR VISION</h2>
<p class="abs vision-copy">To be the leading provider of aerial access, geotechnical drilling, and service solutions, setting the standard for excellence in safety, efficiency, and environmental stewardship.</p>
<a class="btn" href="#" style="left:110px;top:3129px;width:155px;height:38px;line-height:38px">READ MORE</a>
<div class="abs" style="left:702px;top:2920px;width:330px;height:259px;background:#f1b9bb"></div>
<div class="abs" style="left:694px;top:2912px;width:330px;height:259px;background:var(--red)"></div>
<div class="abs" role="img" aria-label="Lift truck on a muddy forest road among green trees" style="left:676px;top:2892px;width:330px;height:259px;background:linear-gradient(180deg,#4f6a3c,#7c9a5a 45%,#8b7d66)"></div>

<svg class="abs" style="left:0;top:3250px" width="1200" height="401" viewBox="0 0 1200 401">
  <polygon points="0,139 106,6 450,71 1200,137 1200,401 0,401" fill="#0b0b0b"/>
  <polygon points="0,139 106,6 450,71 110,35 0,162" fill="#e31e24"/>
</svg>
<div class="brand" style="left:0;top:3415px;width:1200px;text-align:center;font-size:56px;color:var(--white)">MARLOWBY</div>
<div class="abs footer-nav">
  <span>HOME</span><span class="sep"></span>
  <span>ABOUT US</span><span class="sep"></span>
  <span>SERVICES</span><span class="sep"></span>
  <span>SELECT DIVISION</span><span class="sep"></span>
  <span>MISSION</span>
</div>
<div class="abs" style="left:111px;top:3596px;width:978px;height:1px;background:#fff"></div>
<p class="abs copyright">Copyright © 2024 Marlowby. All Rights Reserved</p>

</body>
</html>
```